OpenHarbor Yoga Website Design

Business Logo - attached
5 pages being:
Home
About
Classes
Blog
Contact

Would like Scrolling webpage and yoga symbols to be used.

Must have's being:
Easy to navigate, Text needs to be able to be edited/updated, Enquire Now Links, More Information Links, be a secure site, SEO,

Please refer to attached document for the information for the body of the website.

Target Market(s)

Educators, Community Service, Health and Wellbeing, Mental Health

Industry/Entity Type

Yoga

Coding

Coded - Design and coding required

Number of Pages Required

5+ page

Font styles to use
Other font styles liked:
• Bella Bold BC

Colors
0094D4
00A9DD
6FCCEA
C7EBF8
E9F6FB
6B429C
8869AF
B7A5CE
E3DAEB
F3F0F8

Requirements
Must have
• Easy to navigate, Text needs to be able to be edited/updated, Enquire Now Links, More Information Links, be a secure site, SEO,
Nice to have
• Scrolling webpage, yoga symbols

```html
<!DOCTYPE html>
<html lang="en">
<head>
<meta charset="utf-8">
<title>OpenHarbor Yoga</title>
<link href="https://fonts.googleapis.com/css2?family=Kaushan+Script&family=Manrope:wght@400;500;700&display=swap" rel="stylesheet">
<style>
:root{
  --blue:#0094D4;--cyan:#00A9DD;--sky:#6FCCEA;--ice:#C7EBF8;--mist:#E9F6FB;
  --purple:#6B429C;--violet:#8869AF;--lilac:#B7A5CE;--lavender:#E3DAEB;--pale:#F3F0F8;
  --ink:#3a3a3a;--white:#fff;--black:#000;
  --script:'Kaushan Script',cursive;--sans:'Manrope',sans-serif;
}
*{margin:0;padding:0;box-sizing:border-box}
html,body{width:1200px;height:2823px;overflow:hidden;background:var(--white);font-family:var(--sans)}
.page{position:relative;width:1200px;height:2823px}
.abs{position:absolute}
.site-header{left:0;top:0;width:1200px;height:144px;background:linear-gradient(180deg,#5b3f9c 0%,#3f7fc4 45%,var(--sky) 100%);z-index:2}
.brand{left:120px;top:58px;display:flex;align-items:center;gap:8px;color:var(--white);font-size:17px;font-weight:700}
.brand-dot{width:14px;height:14px;border-radius:50%;background:var(--lilac)}
.contact-item{display:flex;align-items:center;gap:12px;color:var(--white);font-size:16px;font-weight:700;top:16px}
.icon-circle{width:52px;height:52px;border-radius:50%;background:var(--white);border:3px solid var(--ice);display:flex;align-items:center;justify-content:center}
.main-nav{top:88px;left:529px;display:flex;gap:52px;color:var(--white);font-size:19px;font-weight:700}
.hero{left:0;top:144px;width:1200px;height:599px;border-radius:0 0 90px 90px;background:linear-gradient(160deg,#2bb7e3 0%,#1b8fb8 45%,#2a9aa3 80%,#4aa77f 100%);overflow:hidden}
.hero-frame{left:112px;top:64px;width:500px;height:469px;border:0;background:var(--sky);opacity:.55;border-radius:60px 0 170px 0}
.hero-photo{left:112px;top:74px;width:488px;height:459px;border-radius:60px 0 160px 0;background:linear-gradient(135deg,#e9ddd0 0%,#c9b8d8 55%,#a98f76 100%)}
.script{font-family:var(--script);color:var(--purple);font-weight:400}
.welcome{left:653px;top:96px;font-size:32px}
.hero-title{left:653px;top:140px;font-size:54px}
.hero-text{left:653px;top:226px;width:450px;color:var(--white);font-size:21px;line-height:42px;font-weight:500}
.btn{display:flex;align-items:center;justify-content:center;background:var(--purple);color:var(--white);font-family:var(--script);font-size:32px;border-radius:0 40px 0 40px}
.hero-btn{left:653px;top:378px;width:231px;height:67px}
.benefits-title{left:0;top:822px;width:1200px;text-align:center;font-size:40px}
.benefits-text{left:160px;top:891px;width:880px;text-align:center;color:var(--ink);font-size:21px;line-height:42px}
.card-photo{top:1061px;width:309px;height:408px;border-radius:0 0 70px 0}
.card-title{top:1494px;font-size:32px}
.card-text{top:1550px;color:var(--ink);font-size:21px;line-height:35px}
.arrow-btn{top:1647px;width:62px;height:50px;border-radius:0 0 22px 0;background:linear-gradient(90deg,var(--purple),var(--cyan));display:flex;align-items:center;justify-content:center}
.about{left:0;top:1792px;width:1200px;height:600px;border-radius:0 0 90px 0;background:linear-gradient(100deg,var(--pale) 0%,var(--mist) 35%,#e7d3d9 60%,#d89a85 85%,#9c7d8c 100%);overflow:hidden}
.about-title{left:0;top:80px;width:543px;text-align:right;font-size:44px}
.about-text{left:120px;top:140px;width:423px;text-align:right;color:var(--ink);font-size:21px;line-height:38.5px}
.about-btn{left:312px;top:455px;width:231px;height:67px}
.about-frame{left:624px;top:82px;width:464px;height:459px;background:var(--purple);border-radius:70px 0 90px 0}
.about-photo{left:608px;top:66px;width:467px;height:459px;border-radius:70px 0 0 0;background:linear-gradient(180deg,#f1f0ee 0%,#e4e2df 55%,#8d8d8f 100%)}
.site-footer{left:0;top:2392px;width:1200px;height:431px;background:var(--black);color:var(--white)}
.foot-contact{top:70px;display:flex;align-items:center;gap:18px;font-size:16px;font-weight:700}
.foot-brand{left:0;top:82px;width:1200px;text-align:center;font-size:20px;font-weight:700;color:var(--lilac)}
.abn{left:0;top:188px;width:1200px;text-align:center;font-size:17px;font-weight:700}
.foot-nav{left:0;top:239px;width:1200px;display:flex;justify-content:center;gap:46px;font-size:18px;font-weight:700}
.social{top:293px;width:29px;height:29px;border-radius:4px}
.copyright{left:0;top:357px;width:1200px;text-align:center;font-size:15px;font-weight:700}
</style>
</head>
<body>
<div class="page">
  <header class="site-header abs">
    <div class="brand abs"><span class="brand-dot"></span>OpenHarbor Yoga</div>
    <div class="contact-item abs" style="left:506px">
      <span class="icon-circle"><svg width="24" height="24" viewBox="0 0 24 24"><path d="M6.6 10.8a15 15 0 0 0 6.6 6.6l2.2-2.2a1 1 0 0 1 1-.25 11.4 11.4 0 0 0 3.6.6 1 1 0 0 1 1 1V20a1 1 0 0 1-1 1A17 17 0 0 1 3 4a1 1 0 0 1 1-1h3.5a1 1 0 0 1 1 1c0 1.25.2 2.45.6 3.6a1 1 0 0 1-.25 1z" fill="#0094D4"/></svg></span>0400 123 456
    </div>
    <div class="contact-item abs" style="left:753px">
      <span class="icon-circle"><svg width="24" height="24" viewBox="0 0 24 24"><rect x="2" y="5" width="20" height="14" rx="2" fill="#0094D4"/><path d="M3 6l9 7 9-7" stroke="#fff" stroke-width="1.6" fill="none"/></svg></span>INFO@OPENHARBORYOGA.EXAMPLE
    </div>
    <nav class="main-nav abs"><span>HOME</span><span>ABOUT</span><span>CLASSES</span><span>BLOG</span><span>CONTACT</span></nav>
  </header>

  <section class="hero abs">
    <div class="hero-frame abs"></div>
    <div class="hero-photo abs" role="img" aria-label="Smiling woman in lilac activewear sitting on a studio floor"></div>
    <div class="welcome script abs">Welcome to</div>
    <h1 class="hero-title script abs">OpenHarbor Yoga...</h1>
    <p class="hero-text abs">OpenHarbor Yoga believe that you are never too young to benefit from and fall in love with yoga.</p>
    <a class="btn hero-btn abs">Enquire Now</a>
  </section>

  <h2 class="benefits-title script abs">Benefits of Yoga...</h2>
  <p class="benefits-text abs">The benefits of yoga can last a lifetime. It is my aim &amp; passion to introduce yoga to kids of all ages and backgrounds so that they can not only experience the benefits of yoga but fall in love with the practice.</p>

  <div class="card-photo abs" style="left:112px;background:linear-gradient(180deg,#e8e2d8,#bfb3a3 60%,#8b8074)" role="img" aria-label="Woman meditating cross-legged in a bright room"></div>
  <div class="card-photo abs" style="left:445px;background:linear-gradient(180deg,#bcc7d2 0%,#e0b58a 60%,#5a3b2a 100%)" role="img" aria-label="Woman with raised arms at sunset"></div>
  <div class="card-photo abs" style="left:778px;background:linear-gradient(180deg,#b8d6e6 0%,#4f7a48 45%,#6e8ea0 100%)" role="img" aria-label="Person meditating on a jetty by a mountain lake"></div>

  <h3 class="card-title script abs" style="left:112px">Healthy bodies</h3>
  <h3 class="card-title script abs" style="left:445px">Healthy minds</h3>
  <h3 class="card-title script abs" style="left:778px">Healthy spirits</h3>
  <p class="card-text abs" style="left:112px">Develops strong, flexible<br>and healthy bodies</p>
  <p class="card-text abs" style="left:445px">Cultivates confidence<br>and self-esteem</p>
  <p class="card-text abs" style="left:778px">Fosters creativity,<br>expression &amp; imagination</p>
  <a class="arrow-btn abs" style="left:112px"><svg width="26" height="20" viewBox="0 0 26 20"><path d="M2 10h21M15 3l8 7-8 7" stroke="#fff" stroke-width="2.2" fill="none"/></svg></a>
  <a class="arrow-btn abs" style="left:445px"><svg width="26" height="20" viewBox="0 0 26 20"><path d="M2 10h21M15 3l8 7-8 7" stroke="#fff" stroke-width="2.2" fill="none"/></svg></a>
  <a class="arrow-btn abs" style="left:778px"><svg width="26" height="20" viewBox="0 0 26 20"><path d="M2 10h21M15 3l8 7-8 7" stroke="#fff" stroke-width="2.2" fill="none"/></svg></a>

  <section class="about abs">
    <h2 class="about-title script abs">About Us</h2>
    <p class="about-text abs">I decided to combine my passion for mental health, wanting to make a difference in today's youth, with giving back to the community and my love for yoga. This led to me completing my teacher's training in children's Yoga through Calm Kids Yoga Academy.</p>
    <a class="btn about-btn abs">Learn More</a>
    <div class="about-frame abs"></div>
    <div class="about-photo abs" role="img" aria-label="Woman in white top meditating in lotus pose in a living room"></div>
  </section>

  <footer class="site-footer abs">
    <div class="foot-contact abs" style="left:112px">
      <span class="icon-circle"><svg width="22" height="26" viewBox="0 0 22 26"><path d="M11 1a9 9 0 0 0-9 9c0 7 9 15 9 15s9-8 9-15a9 9 0 0 0-9-9z" fill="#0094D4"/><circle cx="11" cy="10" r="3.3" fill="#fff"/></svg></span>HARBOURSIDE, VICTORIA AUSTRALIA 3000
    </div>
    <div class="foot-brand abs">OpenHarbor Yoga</div>
    <div class="foot-contact abs" style="left:746px">
      <span class="icon-circle"><svg width="24" height="24" viewBox="0 0 24 24"><rect x="2" y="5" width="20" height="14" rx="2" fill="#0094D4"/><path d="M3 6l9 7 9-7" stroke="#fff" stroke-width="1.6" fill="none"/></svg></span>INFO@OPENHARBORYOGA.EXAMPLE
    </div>
    <div class="abn abs">ABN:&nbsp; 12 345 678 901</div>
    <nav class="foot-nav abs"><span>HOME</span><span>ABOUT</span><span>CLASSES</span><span>BLOG</span><span>CONTACT</span><span>MORE INFORMATION</span></nav>
    <span class="social abs" style="left:563px;background:var(--blue)"></span>
    <span class="social abs" style="left:607px;background:var(--violet)"></span>
    <div class="copyright abs">@2023 COPYRIGHTS. OPENHARBOR YOGA. ALL RIGHTS RESERVED.</div>
  </footer>
</div>
</body>
</html>
```